Hvac and insulation company needs good looking business card design

We are hvac and insulation company and looking for a new business cards that look to today standards designs

Target Market(s)

homeowners

Industry/Entity Type

Hvac

Contact Information for Business Card

Name: Walter Brinoku
Home comfort consultant
address: 4827 Dunmore St #215 Oakland, CA 94619
office: 888-316-2790
cell: 510-742-3185
Lic.# 584261
Email: walter@corvane-hvac.com
Web: corvane-hvac.com

Requirements
Must have
• clean and sleek look
Nice to have
• simple with a clean look
Should not have
• to busy business card

```html
<!DOCTYPE html>
<html lang="en">
<head>
<meta charset="utf-8">
<title>Corvane Home Solutions – Business Card</title>
<link href="https://fonts.googleapis.com/css2?family=Open+Sans:wght@400;600;700&display=swap" rel="stylesheet">
<style>
  :root {
    --backdrop: #1c1c1c;
    --brand-orange: #f5891f;
    --card-white: #fbfbfb;
    --ink-white: #ffffff;
    --card-radius: 26px;
  }
  * { box-sizing: border-box; margin: 0; padding: 0; }
  html, body {
    width: 1200px; height: 900px; overflow: hidden;
    background: var(--backdrop);
    font-family: "Open Sans", Arial, sans-serif;
  }
  .stage { position: relative; width: 1200px; height: 900px; }
  .card {
    position: absolute; left: 330px;
    width: 540px; height: 309px;
    border-radius: var(--card-radius);
    overflow: hidden;
  }
  .card-front { top: 115px; background: var(--card-white); }
  .card-back  { top: 476px; background: var(--brand-orange); color: var(--ink-white); }

  /* front: wordmark */
  .wordmark {
    position: absolute; inset: 0;
    display: flex; align-items: center; justify-content: center; gap: 16px;
    color: var(--brand-orange);
    font-weight: 700; font-size: 32px; letter-spacing: -0.3px;
    white-space: nowrap;
  }
  .wordmark-square {
    flex: none; width: 34px; height: 34px; background: var(--brand-orange);
  }

  /* back: large mark area */
  .back-mark {
    position: absolute; left: 40px; bottom: 62px;
    display: flex; align-items: center; gap: 14px;
    font-weight: 700; font-size: 38px; color: var(--ink-white);
    white-space: nowrap;
  }
  .back-mark-square { flex: none; width: 48px; height: 48px; background: var(--ink-white); }

  /* back: contact block */
  .contact {
    position: absolute; right: 34px; top: 30px;
    text-align: right; font-size: 14px; line-height: 1.35;
    white-space: nowrap;
  }
  .contact-name { font-weight: 700; font-size: 17px; text-transform: uppercase; letter-spacing: 0.3px; }
  .contact-title { font-size: 14px; margin-bottom: 16px; }
  .contact-line { display: flex; justify-content: flex-end; align-items: center; gap: 8px; }
  .contact-line svg { width: 12px; height: 12px; flex: none; }
  .contact-licence { margin-top: 16px; margin-right: 20px; }
  .contact-address { margin-top: 18px; margin-right: 20px; }
</style>
</head>
<body>
<main class="stage">
  <section class="card card-front" aria-label="Card front">
    <div class="wordmark">
      <span class="wordmark-square"></span>
      <span class="wordmark-name">Corvane Home Solutions</span>
    </div>
  </section>

  <section class="card card-back" aria-label="Card back">
    <div class="back-mark">
      <span class="back-mark-square"></span>
      <span>Corvane</span>
    </div>

    <div class="contact">
      <p class="contact-name">Walter Brinoku</p>
      <p class="contact-title">Home Comfort Consultant</p>
      <p class="contact-line">888-316-2790
        <svg viewBox="0 0 12 12" aria-hidden="true"><path d="M1 4c0-2 2-3 5-3s5 1 5 3l-2 1-1-2H4L3 5zM3 6h6l1 5H2z" fill="#fff"/></svg>
      </p>
      <p class="contact-line">510-742-3185
        <svg viewBox="0 0 12 12" aria-hidden="true"><rect x="2.5" y="0.8" width="7" height="10.4" rx="1.2" fill="none" stroke="#fff" stroke-width="1.4"/></svg>
      </p>
      <p class="contact-line">walter@corvane-hvac.com
        <svg viewBox="0 0 12 12" aria-hidden="true"><rect x="0.5" y="2" width="11" height="8" fill="#fff"/><path d="M0.5 2l5.5 4.5L11.5 2" fill="none" stroke="#f5891f" stroke-width="1.2"/></svg>
      </p>
      <p class="contact-line">corvane-hvac.com
        <svg viewBox="0 0 12 12" aria-hidden="true"><circle cx="6" cy="6" r="5.3" fill="#fff"/><path d="M0.7 6h10.6M6 0.7c-3 3-3 7.6 0 10.6M6 0.7c3 3 3 7.6 0 10.6" fill="none" stroke="#f5891f" stroke-width="0.9"/></svg>
      </p>
      <p class="contact-licence">Lic.# 584261</p>
      <p class="contact-address">4827 Dunmore St #215<br>Oakland, CA 94619</p>
    </div>
  </section>
</main>
</body>
</html>
```